Computer Training in the Education sector - Letterhead

We need a new letter head to be designed for the company. We provide computer training fro the Education Sector, both primary and private tertiary providers. The colours will need to tie in with the website www.crossingthestream.co.nz.
The company name is Crossing the Stream with the tag line of Computer Training for Educators.
The footer will need to have the following detail...
0508 PCS MENTOR
021 839 415
www.crossingthestream.co.nz / training@crossingthestream.co.nz
Updates

Thanks for the designs so far.

Some have watermarks in the background. Please don't worry about using watermarks as I will not be using a watermark in in a final design.
Regards,
Roger

Thank you for all the designs and the effort. There was some great concepts that came through.

Cheers
Roger

Industry/Entity Type

Computer

```html
<!DOCTYPE html>
<html lang="en">
<head>
<meta charset="utf-8">
<title>Crossing the Stream – Letterhead</title>
<link rel="stylesheet" href="https://fonts.googleapis.com/css2?family=Arimo:wght@400;700&display=swap">
<style>
  :root {
    --paper: #ffffff;
    --ink: #2b2b2b;
    --rule: #555555;
    --brand-blue: #2f74b5;
    --brand-green: #8ab743;
  }
  html, body {
    margin: 0;
    padding: 0;
    width: 1034px;
    height: 1200px;
    overflow: hidden;
    background: var(--paper);
  }
  .letterhead {
    position: relative;
    width: 1034px;
    height: 1200px;
    background: var(--paper);
    font-family: "Arimo", Arial, sans-serif;
    color: var(--ink);
  }
  .brand {
    position: absolute;
    left: 58px;
    top: 70px;
    display: flex;
    align-items: center;
    gap: 12px;
  }
  .brand-dot {
    width: 18px;
    height: 18px;
    border-radius: 50%;
    background: var(--brand-blue);
  }
  .brand-name {
    font-size: 26px;
    font-weight: 700;
    color: var(--brand-blue);
    line-height: 1.15;
    width: 150px;
  }
  .contact-rule {
    position: absolute;
    left: 659px;
    top: 53px;
    width: 1px;
    height: 86px;
    background: var(--rule);
  }
  .contact-list {
    position: absolute;
    left: 680px;
    top: 53px;
    margin: 0;
    padding: 0;
    list-style: none;
    font-size: 16.5px;
    letter-spacing: 0.5px;
    line-height: 25.6px;
  }
  .contact-list li {
    display: flex;
    align-items: center;
    gap: 6px;
  }
  .contact-icon {
    width: 13px;
    height: 13px;
    flex: none;
  }
  .tagline {
    position: absolute;
    left: 38px;
    top: 1157px;
    margin: 0;
    font-size: 18.5px;
    font-weight: 400;
    letter-spacing: 2.6px;
    color: var(--ink);
  }
  .corner-decoration {
    position: absolute;
    left: 734px;
    top: 970px;
    width: 300px;
    height: 230px;
    background: linear-gradient(135deg, var(--brand-blue) 0%, var(--brand-green) 100%);
  }
</style>
</head>
<body>
<main class="letterhead">
  <header>
    <div class="brand">
      <span class="brand-dot"></span>
      <span class="brand-name">Crossing the Stream</span>
    </div>
    <div class="contact-rule"></div>
    <ul class="contact-list">
      <li>
        <svg class="contact-icon" viewBox="0 0 16 16"><circle cx="8" cy="8" r="7" fill="none" stroke="#2b2b2b" stroke-width="1.3"/><path d="M5 4.5 L6.8 4.5 L7.3 6.5 L6.3 7.3 Q7 9 8.7 9.7 L9.5 8.7 L11.5 9.2 L11.5 11 Q7.5 11.5 5 7 Z" fill="#2b2b2b"/></svg>
        0508 PCS MENTOR
      </li>
      <li>
        <svg class="contact-icon" viewBox="0 0 16 16"><circle cx="8" cy="8" r="7" fill="none" stroke="#2b2b2b" stroke-width="1.3"/><path d="M5 4.5 L6.8 4.5 L7.3 6.5 L6.3 7.3 Q7 9 8.7 9.7 L9.5 8.7 L11.5 9.2 L11.5 11 Q7.5 11.5 5 7 Z" fill="#2b2b2b"/></svg>
        021 839 415
      </li>
      <li>
        <svg class="contact-icon" viewBox="0 0 16 16"><path d="M1 7 L8 2.5 L15 7 L15 14 L1 14 Z" fill="#2b2b2b"/><path d="M2.5 7.5 L8 11 L13.5 7.5" fill="none" stroke="#fff" stroke-width="1.2"/></svg>
        training@crossingthestream.co.nz
      </li>
      <li>
        <svg class="contact-icon" viewBox="0 0 16 16" fill="none" stroke="#2b2b2b" stroke-width="1.1"><circle cx="8" cy="8" r="7"/><ellipse cx="8" cy="8" rx="3" ry="7"/><path d="M1 8 H15 M2 4.5 H14 M2 11.5 H14"/></svg>
        www.crossingthestream.co.nz
      </li>
    </ul>
  </header>

  <p class="tagline">COMPUTER TRAINING FOR EDUCATORS</p>

  <div class="corner-decoration" role="img" aria-label="Decorative blue and green corner ornament"></div>
</main>
</body>
</html>
```